Need website for LED Signs company

Need an web page for a sign company. Basic home page / Tab for photo gallery (projects), tab for other projects could be photo gallery type with the ability for descriptions gallery to be able to have albums (projects) and tab for about us / testimonials Should be easy for me to change with dreamweaver or easy to change add remove content. I will provide pictures and content I would be happy if it could be set up like a template where i can add the content after but i would provide as much content as possible the current page is http://glowcrestsigns.ca examples of my competition:https://metroled.com/led-message-signs/http://www.libertevision.com/https://www.daktronics.com/en-us/products/message-displaysSEO optimized

1 page

• I want to feature LED signs and EMC's the Special projects tab tab will or should be a photo type gallery that is easy to add photos with detailed descriptions
• I do not want to wast peoples time making something similar to what i have now.
• To help me pick a winner Please show links to some of the sites you have created in the past. .

```html
<!DOCTYPE html>
<html lang="en">
<head>
<meta charset="utf-8">
<title>Glowcrest Signs — LED and Neon</title>
<link href="https://fonts.googleapis.com/css2?family=Montserrat:wght@300;400;500;600;700&family=Open+Sans:wght@400;600;700&display=swap" rel="stylesheet">
<style>
:root{
  --ink:#222;
  --muted:#8a8a8a;
  --white:#fff;
  --paper:#f4f4f4;
  --night:#0b1622;
  --violet:#8a2be2;
  --magenta:#d21fb5;
  --amber:#f5c518;
  --orange:#f08a24;
  --green:#39c34a;
  --steel:#8c8c8c;
  --charcoal:#333;
  --black:#050505;
}
*{box-sizing:border-box;margin:0;padding:0}
html,body{width:1200px;height:5114px;overflow:hidden}
body{position:relative;font-family:"Open Sans",Arial,sans-serif;color:var(--ink);background:var(--white)}
.abs{position:absolute}
section,footer.footer{position:absolute;left:0;width:1200px;overflow:hidden}
.heading{font-family:"Montserrat",Arial,sans-serif;font-weight:600;letter-spacing:4px;text-transform:uppercase;font-size:15px}
.sub{font-size:9px;color:var(--muted)}
.btn-yellow{background:var(--amber);color:var(--white);font-family:"Montserrat",sans-serif;font-size:10px;font-weight:600;letter-spacing:1px;text-align:center;line-height:32px;width:112px;height:32px}

/* hero */
.hero{top:0;height:672px;background:linear-gradient(180deg,#0f2a3a 0%,#0a1a28 55%,#05090f 100%)}
.hero-art{left:60px;top:150px;width:1080px;height:470px;border-radius:10px;
  background:radial-gradient(ellipse at 55% 45%,rgba(120,70,220,.85),rgba(40,90,200,.55) 40%,rgba(20,40,70,0) 72%),
  radial-gradient(ellipse at 15% 60%,rgba(200,40,160,.55),rgba(0,0,0,0) 45%),
  radial-gradient(ellipse at 88% 55%,rgba(30,160,220,.5),rgba(0,0,0,0) 45%)}
.brand{left:60px;top:38px;display:flex;align-items:center;gap:10px;font-family:"Montserrat",sans-serif;font-weight:600;font-size:18px;color:var(--white)}
.brand i{width:22px;height:22px;background:var(--white);display:block}
.nav{left:540px;top:42px;display:flex;gap:24px;font-family:"Montserrat",sans-serif;font-size:10px;font-weight:600;letter-spacing:1px;color:var(--white)}
.nav .menu{margin-left:70px;opacity:.8;display:flex;gap:8px;align-items:center}
.crest{left:575px;top:118px;width:50px;height:50px;border-radius:50%;border:2px solid var(--white)}
.hero-title{left:0;top:300px;width:1200px;text-align:center;font-family:"Montserrat",sans-serif;font-weight:500;font-size:96px;letter-spacing:8px;color:var(--white)}
.hero-lead{left:400px;top:418px;width:400px;text-align:center;font-size:11px;color:#dfe6ee;line-height:1.5}
.hero-bar{left:0;top:624px;width:1200px;height:48px;border-top:1px solid rgba(255,255,255,.12)}
.social{left:232px;top:16px;display:flex;gap:22px;font-size:10px;color:#c9d2dc}
.social span:first-child{color:var(--white)}
.join{left:893px;top:16px;font-family:"Montserrat",sans-serif;font-size:10px;font-weight:600;color:var(--white);letter-spacing:1px}
.scroll{left:596px;top:-8px;width:8px;height:22px;border:1px solid var(--white);border-radius:4px}

/* about */
.about{top:672px;height:470px;background:var(--white)}
.city{left:102px;top:95px;width:443px;height:256px;box-shadow:0 14px 30px rgba(0,0,0,.25);
  background:linear-gradient(180deg,#2b0f55 0%,#4a1a8a 45%,#c0238f 62%,#1a1c63 64%,#3b1d7a 100%)}
.about .kicker{left:575px;top:103px;font-family:"Montserrat",sans-serif;font-size:10px;font-weight:700;letter-spacing:2px;color:var(--amber)}
.about h2{left:575px;top:122px;font-family:"Montserrat",sans-serif;font-weight:400;font-size:30px;color:var(--violet)}
.about .since{left:575px;top:165px;font-size:9px;color:var(--muted)}
.about p{left:575px;top:186px;width:480px;font-size:11px;line-height:1.7;color:#555}
.tags{left:575px;top:268px;display:flex;gap:14px}
.tag{display:flex;align-items:center;gap:8px;font-family:"Montserrat",sans-serif;font-size:12px;font-weight:700}
.tag .dot{width:28px;height:28px;border-radius:50%;border:1px solid #ccc;display:flex;align-items:center;justify-content:center}
.tag.sign{color:var(--amber)} .tag.led{color:var(--green)} .tag.glow{color:var(--violet)}
.outline-btn{left:575px;top:330px;width:118px;height:32px;border:1px solid #999;font-family:"Montserrat",sans-serif;font-size:9px;font-weight:600;letter-spacing:1px;line-height:30px;text-align:center}

/* portfolio head */
.portfolio-head{top:1142px;height:147px;background:var(--paper)}
.portfolio-head .heading{left:232px;top:68px}
.portfolio-head .sub{left:232px;top:90px}
.filters{left:705px;top:74px;display:flex;gap:32px;font-family:"Montserrat",sans-serif;font-size:9px;font-weight:600;letter-spacing:1px;color:#999}
.filters span:first-child{color:var(--ink)}

/* grid */
.grid{top:1289px;height:988px;background:#111}
.tile{position:absolute}
.feature-text{position:absolute;left:140px;top:265px;color:var(--white)}
.feature-text h3{font-family:"Montserrat",sans-serif;font-weight:400;font-size:20px;color:var(--amber);margin-bottom:8px}
.feature-text p{font-size:10px;line-height:1.6;width:300px;color:#ddd;margin-bottom:20px}
.badge{position:absolute;width:60px;height:60px;border-radius:50%;border:2px solid var(--white)}

/* features */
.features{top:2277px;height:587px;background:var(--steel);color:var(--ink)}
.features .heading{left:218px;top:153px}
.features .sub{left:218px;top:175px;color:#444}
.quote{left:218px;top:215px;width:340px;font-size:12px;font-weight:600;line-height:1.6}
.features p.body{left:218px;top:270px;width:340px;font-size:10px;line-height:1.7;color:#333}
.stats{left:218px;top:390px;display:flex;gap:42px}
.stat b{font-family:"Montserrat",sans-serif;font-size:22px;font-weight:500;color:var(--white);display:block}
.stat span{font-size:8px;color:#333}
.feat{position:absolute;width:170px}
.feat svg{display:block;margin-bottom:8px}
.feat h4{font-family:"Montserrat",sans-serif;font-size:12px;font-weight:600;margin-bottom:4px}
.feat p{font-size:9px;line-height:1.5;color:#333}

/* services */
.services{top:2864px;height:477px;background:var(--white)}
.ghost{left:0;top:125px;width:1200px;text-align:center;font-family:"Montserrat",sans-serif;font-size:26px;font-weight:300;letter-spacing:10px;color:#eee}
.service{position:absolute;top:225px;width:250px;padding-left:34px}
.service svg{position:absolute;left:0;top:0}
.service h4{font-family:"Montserrat",sans-serif;font-size:15px;font-weight:600;margin-bottom:8px}
.service p{font-size:10px;line-height:1.6;margin-bottom:14px}
.service .more{font-family:"Montserrat",sans-serif;font-size:13px;font-weight:700}
.s1 h4,.s1 .more{color:var(--magenta)} .s1 p{color:var(--violet)}
.s2 h4,.s2 .more{color:var(--amber)} .s2 p{color:var(--amber)}
.s3 h4{color:var(--orange)} .s3 p{color:var(--orange)} .s3 .more{color:var(--magenta)}

/* testimonials */
.testimonials{top:3341px;height:521px;background:var(--paper)}
.testimonials .heading{left:0;width:1200px;top:100px;text-align:center}
.testimonials .sub{left:0;width:1200px;top:122px;text-align:center}
.testimonials .lead{left:360px;top:145px;width:480px;text-align:center;font-size:10px;line-height:1.6;color:#555}
.card{position:absolute;top:240px;width:232px;height:158px;background:var(--white);padding:22px 20px;box-shadow:0 2px 8px rgba(0,0,0,.05)}
.card .avatar{position:absolute;left:20px;top:22px;width:46px;height:46px;border-radius:50%;background:#222;color:var(--white);font-size:9px;font-weight:700;line-height:46px;text-align:center}
.card .who{position:absolute;left:78px;top:30px;font-size:8px;color:var(--muted)}
.card h5{position:absolute;left:78px;top:42px;font-size:11px;font-weight:600}
.card p{position:absolute;left:20px;top:86px;width:192px;font-size:9px;line-height:1.6;color:#666}
.dots{left:572px;top:436px;width:56px;border-top:1px solid #aaa}

/* news */
.news{top:3862px;height:375px;background:var(--white)}
.news .title{left:218px;top:36px;font-family:"Montserrat",sans-serif;font-size:13px;font-weight:600}
.news .title span{font-family:"Open Sans",sans-serif;font-weight:400;font-size:9px;color:var(--muted);margin-left:12px}
.news .view{left:870px;top:38px;font-size:9px;color:var(--muted)}
.post{position:absolute;top:75px;width:232px}
.post .photo{height:188px}
.post .meta{font-size:8px;color:var(--muted);margin:10px 0 6px}
.post h6{font-size:11px;font-weight:600;line-height:1.4}
.post p{font-size:8px;color:#999;margin-top:8px;line-height:1.5}

/* subscribe */
.subscribe{top:4237px;height:144px;background:var(--charcoal);color:var(--white)}
.subscribe .heading{left:239px;top:54px;font-size:14px}
.subscribe .sub{left:239px;top:76px;color:#aaa}
.field{position:absolute;top:58px;height:30px;border:1px solid #666;font-size:9px;color:#aaa;padding:0 10px;line-height:28px}
.subscribe .go{left:862px;top:58px;width:83px;height:30px;background:var(--white);color:var(--ink);font-size:9px;font-weight:700;letter-spacing:1px;text-align:center;line-height:30px}

/* footer */
.footer{top:4381px;height:228px;background:var(--black);color:#aaa}
.footer .note{left:0;width:1200px;top:68px;text-align:center;font-size:9px}
.partners{left:215px;top:120px;display:flex;gap:22px;align-items:center}
.partner{width:128px;height:56px;display:flex;align-items:center;justify-content:center}
.partner.on{background:var(--white)}
.partner i{display:block;width:26px;height:26px;border-radius:50%;border:1px solid #777}
.partner.on i{border-color:var(--amber);background:var(--amber)}

/* landscape */
.landscape{top:4609px;height:505px;background:linear-gradient(180deg,#fafafa 0%,#6e6f70 40%,#3e4a4d 65%,#1f2a2a 100%)}
</style>
</head>
<body>

<section class="hero">
  <div class="abs hero-art" role="img" aria-label="Glowing 3D cube of LED screens over a mountain night sky"></div>
  <div class="abs brand"><i></i>Glowcrest</div>
  <nav class="abs nav">
    <span>HOME</span><span>ABOUT</span><span>SERVICES</span><span>PORTFOLIO</span><span>BLOG</span><span>CONTACT</span>
    <span class="menu">MENU
      <svg width="10" height="10" viewBox="0 0 10 10"><circle cx="4" cy="4" r="3" fill="none" stroke="#fff" stroke-width="1.3"/><line x1="6.3" y1="6.3" x2="9.5" y2="9.5" stroke="#fff" stroke-width="1.3"/></svg>
    </span>
  </nav>
  <div class="abs crest"></div>
  <h1 class="abs hero-title">LED AND NEON</h1>
  <p class="abs hero-lead">Custom LED and neon signage built to shine day and night for shops, venues and events.</p>
  <div class="abs hero-bar">
    <div class="abs scroll"></div>
    <div class="abs social"><span>Linkwave</span><span>Chirpline</span><span>Workfolio</span><span>Circleplus</span></div>
    <div class="abs join">JOIN US NOW &#8594;</div>
  </div>
</section>

<section class="about">
  <div class="abs city" role="img" aria-label="Neon city skyline reflected on water"></div>
  <div class="abs kicker">WHY WE ARE</div>
  <h2 class="abs">Signage Studio 1980</h2>
  <div class="abs since">Since 1980</div>
  <p class="abs">Lorem ipsum dolor sit amet, consectetuer adipiscing elit diam sed diam nonummy nibh euismod tincidunt ut laoreet dolore magna aliquam erat volutpat. Ut wisi enim ad minim veniam quis nostrud.</p>
  <div class="abs tags">
    <div class="tag sign"><span class="dot"><svg width="12" height="12" viewBox="0 0 12 12"><path d="M2 10 L9 3 M7 2 L10 5" stroke="#333" stroke-width="1.3" fill="none"/></svg></span>NEON SIGN</div>
    <div class="tag led"><span class="dot"><svg width="12" height="12" viewBox="0 0 12 12"><rect x="2" y="3" width="8" height="6" fill="none" stroke="#333" stroke-width="1.3"/></svg></span>NEON LED</div>
    <div class="tag glow"><span class="dot"><svg width="12" height="12" viewBox="0 0 12 12"><circle cx="6" cy="6" r="3.5" fill="none" stroke="#333" stroke-width="1.3"/></svg></span>GLOW SIGNS</div>
  </div>
  <div class="abs outline-btn">MORE WITH US</div>
</section>

<section class="portfolio-head">
  <div class="abs heading">Our Portfolio</div>
  <div class="abs sub">Latest projects completed</div>
  <div class="abs filters"><span>ALL WORK</span><span>BRANDING</span><span>WEB DESIGN</span><span>OTHER</span></div>
</section>

<section class="grid">
  <div class="tile" style="left:0;top:0;width:600px;height:508px;background:radial-gradient(ellipse at 60% 45%,#8a6a5a,#3a3a40 55%,#1c1d22)" role="img" aria-label="Glowing stag on a dark smoky background">
    <div class="badge" style="left:270px;top:120px"></div>
    <div class="feature-text"><h3>Neon Design 2016</h3><p>Lorem ipsum dolor sit amet, consectetuer adipiscing elit sed diam nonummy nibh euismod tincidunt.</p><div class="btn-yellow">READ MORE</div></div>
  </div>
  <div class="tile" style="left:600px;top:0;width:300px;height:254px;background:linear-gradient(135deg,#1a1a22,#b0205a 55%,#20a8c0)" role="img" aria-label="Crossed neon light swords artwork"></div>
  <div class="tile" style="left:900px;top:0;width:300px;height:254px;background:linear-gradient(135deg,#2a1050,#d8287a 50%,#f0d020)" role="img" aria-label="Neon sale lettering artwork"></div>
  <div class="tile" style="left:600px;top:254px;width:300px;height:254px;background:linear-gradient(90deg,#2ad0e0,#e03070,#f0c020,#40d050,#a040e0)" role="img" aria-label="Row of colourful neon light tubes"></div>
  <div class="tile" style="left:900px;top:254px;width:300px;height:254px;background:linear-gradient(135deg,#1a0830,#5a1a8a 55%,#c030a0)" role="img" aria-label="Purple neon follow lettering artwork"></div>
  <div class="tile" style="left:0;top:508px;width:300px;height:240px;background:linear-gradient(135deg,#0a1a30,#103060 60%,#c02030)" role="img" aria-label="Neon holiday figure greeting artwork"></div>
  <div class="tile" style="left:300px;top:508px;width:300px;height:220px;background:linear-gradient(135deg,#0c0c14,#3a1050 50%,#2a6040)" role="img" aria-label="Set of neon casino and poker signs"></div>
  <div class="tile" style="left:0;top:748px;width:300px;height:240px;background:radial-gradient(ellipse at 60% 50%,#a01030,#2a0810 70%)" role="img" aria-label="Red neon holiday tree artwork"></div>
  <div class="tile" style="left:300px;top:728px;width:300px;height:260px;background:radial-gradient(ellipse at 50% 50%,#f060a0,#7a1870 45%,#1a0a2a)" role="img" aria-label="Pink neon light tunnel artwork"></div>
  <div class="tile" style="left:600px;top:508px;width:600px;height:480px;background:radial-gradient(ellipse at 45% 45%,#7a6a5a,#34363c 55%,#1a1b20)" role="img" aria-label="Glowing stag on a dark smoky background">
    <div class="badge" style="left:250px;top:90px"></div>
    <div class="feature-text" style="left:270px;top:200px"><h3>Signage Design 2016</h3><p>Lorem ipsum dolor sit amet, consectetuer adipiscing elit sed diam nonummy nibh euismod tincidunt.</p><div class="btn-yellow">READ MORE</div></div>
  </div>
</section>

<section class="features">
  <div class="abs heading">Our Features</div>
  <div class="abs sub">Lorem ipsum dolor sit amet</div>
  <div class="abs quote">"Our will get the best support consectetuer adipiscing elit sed diam nonummy nibh euismod tincidunt."</div>
  <p class="abs body">Lorem ipsum dolor sit amet, consectetuer adipiscing elit sed diam nonummy nibh euismod tincidunt ut laoreet dolore magna aliquam erat volutpat ut wisi enim ad minim veniam quis nostrud exerci tation.</p>
  <div class="abs stats">
    <div class="stat"><b>25</b><span>Years</span></div>
    <div class="stat"><b>15</b><span>Awards</span></div>
    <div class="stat"><b>10</b><span>Offices</span></div>
    <div class="stat"><b>127</b><span>Projects</span></div>
  </div>
  <div class="feat" style="left:630px;top:225px">
    <svg width="22" height="22" viewBox="0 0 22 22"><rect x="3" y="3" width="16" height="16" fill="none" stroke="#333" stroke-width="1.4"/></svg>
    <h4>Creative Ideas</h4><p>Lorem ipsum dolor sit amet consectetuer adipiscing.</p></div>
  <div class="feat" style="left:818px;top:225px">
    <svg width="22" height="22" viewBox="0 0 22 22"><circle cx="11" cy="11" r="8" fill="none" stroke="#333" stroke-width="1.4"/></svg>
    <h4>Creative Ideas</h4><p>Lorem ipsum dolor sit amet consectetuer adipiscing.</p></div>
  <div class="feat" style="left:630px;top:375px">
    <svg width="22" height="22" viewBox="0 0 22 22"><path d="M11 2 V20 M2 11 H20" stroke="#333" stroke-width="1.4"/></svg>
    <h4>Creative Ideas</h4><p>Lorem ipsum dolor sit amet consectetuer adipiscing.</p></div>
  <div class="feat" style="left:818px;top:375px">
    <svg width="22" height="22" viewBox="0 0 22 22"><path d="M4 17 L11 4 L18 17 Z" fill="none" stroke="#333" stroke-width="1.4"/></svg>
    <h4>Motion Graphic</h4><p>Lorem ipsum dolor sit amet consectetuer adipiscing.</p></div>
</section>

<section class="services">
  <div class="abs ghost">OUR SERVICES</div>
  <div class="service s1" style="left:211px">
    <svg width="22" height="22" viewBox="0 0 22 22"><rect x="2" y="2" width="18" height="18" fill="none" stroke="#d21fb5" stroke-width="1.5"/></svg>
    <h4>Multi Concept</h4><p>Lorem ipsum dolor sit amet consectetuer adipiscing elit sed diam nonummy nibh euismod.</p><div class="more">READ MORE</div></div>
  <div class="service s2" style="left:475px">
    <svg width="22" height="22" viewBox="0 0 22 22"><circle cx="11" cy="11" r="9" fill="none" stroke="#f5c518" stroke-width="1.5"/></svg>
    <h4>Professional Team</h4><p>Lorem ipsum dolor sit amet consectetuer adipiscing elit sed diam nonummy nibh euismod.</p><div class="more">READ MORE</div></div>
  <div class="service s3" style="left:716px">
    <svg width="22" height="22" viewBox="0 0 22 22"><circle cx="11" cy="11" r="9" fill="none" stroke="#f08a24" stroke-width="1.5"/><path d="M7 11 L10 14 L15 8" stroke="#f08a24" stroke-width="1.5" fill="none"/></svg>
    <h4>The Best Marketing...</h4><p>Lorem ipsum dolor sit amet consectetuer adipiscing elit sed diam nonummy nibh euismod.</p><div class="more">READ MORE</div></div>
</section>

<section class="testimonials">
  <div class="abs heading">What They Say</div>
  <div class="abs sub">About our clients and partners</div>
  <p class="abs lead">Lorem ipsum dolor sit amet, consectetuer adipiscing elit sed diam nonummy nibh euismod tincidunt ut laoreet dolore magna aliquam erat volutpat.</p>
  <div class="card" style="left:225px"><div class="avatar">75X75</div><span class="who">Client</span><h5>Brightfold Lab</h5><p>Lorem ipsum dolor sit amet, consectetuer adipiscing elit sed diam nonummy nibh euismod.</p></div>
  <div class="card" style="left:484px"><div class="avatar">75X75</div><span class="who">Client</span><h5>Norvel Crafts</h5><p>Lorem ipsum dolor sit amet, consectetuer adipiscing elit sed diam nonummy nibh euismod.</p></div>
  <div class="card" style="left:743px"><div class="avatar">75X75</div><span class="who">Client</span><h5>Marisol Tevane</h5><p>Lorem ipsum dolor sit amet, consectetuer adipiscing elit sed diam nonummy nibh euismod.</p></div>
  <div class="abs dots"></div>
</section>

<section class="news">
  <div class="abs title">Latest news<span>Latest news from our blog</span></div>
  <div class="abs view">View Articles &#8594;</div>
  <article class="post" style="left:218px"><div class="photo" role="img" aria-label="Green hills under a hazy sky" style="background:linear-gradient(180deg,#c9cfd0,#8a9a78 55%,#3e4a30)"></div><div class="meta">DESIGN · JAN 2016 · NEWS</div><h6>An Winner Eco-friendly awarded packaging 2014 – 2015</h6><p>Lorem ipsum dolor sit amet consectetuer adipiscing elit.</p></article>
  <article class="post" style="left:484px"><div class="photo" role="img" aria-label="Volcanic valley at dawn" style="background:linear-gradient(180deg,#d8c8a8,#8a7a68 55%,#3a3430)"></div><div class="meta">DESIGN · JAN 2016 · NEWS</div><h6>An Winner Eco-friendly awarded packaging 2014 – 2015</h6><p>Lorem ipsum dolor sit amet consectetuer adipiscing elit.</p></article>
  <article class="post" style="left:750px"><div class="photo" role="img" aria-label="Lake at sunset between forests" style="background:linear-gradient(180deg,#5a6a80,#e0a060 50%,#2a3030)"></div><div class="meta">DESIGN · JAN 2016 · NEWS</div><h6>An Winner Eco-friendly awarded packaging 2014 – 2015</h6><p>Lorem ipsum dolor sit amet consectetuer adipiscing elit.</p></article>
</section>

<section class="subscribe">
  <div class="abs heading">Subscribe Now</div>
  <div class="abs sub">Subscribe to our newsletter</div>
  <div class="field" style="left:528px;width:172px">Your name</div>
  <div class="field" style="left:713px;width:140px">Your email address</div>
  <div class="abs go">SUBSCRIBE</div>
</section>

<footer class="footer">
  <div class="abs note">Powered by Glowcrest Signs</div>
  <div class="abs partners">
    <div class="partner"><i></i></div>
    <div class="partner on"><i></i></div>
    <div class="partner"><i></i></div>
    <div class="partner"><i></i></div>
    <div class="partner"><i></i></div>
  </div>
</footer>

<section class="landscape" role="img" aria-label="Misty mountain valley with pine forest under cloudy sky"></section>

</body>
</html>
```